Professional Single Page Website Design for Tollbrook Advisory

Tollbrook Advisory is a new business consultancy specializing in providing expert services to small businesses, primarily in the brick-and-mortar retail and food service sectors. We offer a range of services including franchise development and launch, due diligence, and construction management.

Currently, we have a basic website set up at www.tollbrookadvisory.example, but we need a professional touch to enhance its design and functionality.

Project Requirements:
- Single Page Design: For now, we need a single page design that effectively showcases who we are, our services, and contact information.
- Future Expansion: The design should be flexible and scalable for future expansion to include additional pages like specific service offerings, about us, and a dedicated contact page.
- Design Aesthetic: We are looking for a modern yet professional design that aligns with our brand identity.
- Logo: We have a logo that we like, which was also sourced from Pixel Bazaar. The logo files are attached to this project brief.

Key Sections to Include:
- Hero Section: An engaging introduction to Tollbrook Advisory with a strong visual impact.
- About Us: A brief overview of who we are and our mission.
- Team: Section for the profiles of the two principals.
- Services: A clear and concise presentation of our services, including franchise development, due diligence, and construction management.
- Contact Information: Easy-to-find contact details, including a form for inquiries.
- Call to Action: Encouraging visitors to get in touch with us for consultations or further information.

Design Considerations:
- Ensure the design is responsive and mobile-friendly.
- Include high-quality images and icons that complement our services and industry.
- We do not need development services, this is only a design project.

```html
<!DOCTYPE html>
<html lang="en">
<head>
<meta charset="utf-8">
<title>Tollbrook Advisory — Building Success in Southern California</title>
<link rel="stylesheet" href="https://fonts.googleapis.com/css2?family=Poppins:wght@600;700&family=Roboto:wght@400;500;700&display=swap">
<style>
:root{
  --navy:#1f2a35;
  --navy-2:#26323e;
  --mint:#8cc5a8;
  --mint-dark:#6fb08f;
  --ink:#1b1b1b;
  --body:#666b70;
  --card:#f4f4f4;
  --light:#f3f4f4;
  --black:#0c0c0c;
  --white:#ffffff;
}
*{margin:0;padding:0;box-sizing:border-box}
html,body{width:1200px;height:3354px;overflow:hidden}
body{position:relative;background:var(--white);font-family:"Roboto",Arial,sans-serif;color:var(--body)}
.abs{position:absolute}
.heading{font-family:"Poppins",Arial,sans-serif;font-weight:700;color:var(--ink)}
.btn{position:absolute;display:flex;align-items:center;justify-content:center;gap:8px;background:var(--mint);color:var(--white);font-weight:700;font-size:15px;text-transform:uppercase;letter-spacing:.2px}
.btn .dot{width:14px;height:14px;border-radius:50%;background:var(--white);position:relative}
.btn .dot::after{content:"";position:absolute;left:4px;top:4px;border-left:6px solid var(--mint);border-top:3px solid transparent;border-bottom:3px solid transparent}

/* header */
.topbar{left:0;top:0;width:1200px;height:50px}
.brand{left:143px;top:20px;display:flex;align-items:center;gap:12px}
.brand-mark{width:62px;height:62px;border-radius:50%;border:6px solid var(--mint)}
.brand-name{font-family:"Poppins",sans-serif;font-weight:600;font-size:21px;color:var(--navy);line-height:1.1}
.contact-chip{top:7px;display:flex;align-items:center;gap:12px;color:var(--white)}
.chip-icon{width:34px;height:34px;border:1.5px solid #9aa5ae;border-radius:5px;display:flex;align-items:center;justify-content:center}
.chip-label{font-size:12px;line-height:14px}
.chip-value{font-size:16px;font-weight:500;line-height:20px}
.login{left:968px;top:9px;width:88px;height:34px;background:var(--mint);color:var(--white);font-size:13px;font-weight:500;display:flex;align-items:center;justify-content:center;border-radius:2px}
.mainnav{top:74px;left:493px;display:flex;gap:0;font-size:14px;font-weight:500;color:var(--ink)}
.mainnav span{margin-right:64px}

/* hero */
.hero-title{left:142px;top:192px;font-size:44px;line-height:53px;color:var(--white)}
.hero-title em{font-style:normal;color:var(--mint)}
.hero-sub{left:143px;top:311px;font-size:17px;color:var(--white)}

/* about */
.about-title{left:644px;top:738px;font-size:37px}
.about-text{left:644px;top:800px;width:411px;font-size:13.4px;line-height:24px;text-align:justify}
.about-text p+p{margin-top:8px}

/* services */
.section-title{width:1200px;left:0;text-align:center;font-size:37px}
.section-title span{color:var(--navy-2)}
.service{top:1278px;width:291px;height:251px;background:var(--card);text-align:center;padding:32px 14px 0}
.service.active{border-bottom:4px solid var(--mint);height:256px}
.svc-icon{width:82px;height:82px;border-radius:50%;margin:0 auto 20px;background:var(--navy);display:flex;align-items:center;justify-content:center}
.svc-icon.mint{background:var(--mint)}
.svc-name{font-size:17.5px;font-weight:500;color:var(--ink);margin-bottom:10px}
.svc-desc{font-size:13px;line-height:21px;padding:0 12px}
.arrow{top:1383px;width:40px;height:40px;border-radius:50%;background:#4a4d50;display:flex;align-items:center;justify-content:center}

/* cta */
.cta{left:0;top:1620px;width:1200px;height:274px;background:linear-gradient(180deg,var(--navy-2),#1d2832)}
.cta-title{width:1200px;left:0;top:1663px;text-align:center;font-size:37px;color:var(--white)}
.cta-text{left:150px;width:900px;top:1726px;text-align:center;color:var(--white);font-size:14px;line-height:24px;font-weight:500}

/* team */
.member-name{left:143px;top:2058px;font-size:21px;font-weight:500;color:var(--ink)}
.member-role{left:143px;top:2092px;font-size:16px}
.member-mail{left:143px;top:2126px;font-size:13.5px;color:var(--ink);text-decoration:underline;display:flex;align-items:center;gap:8px}
.member-bio{left:143px;top:2156px;width:245px;font-size:13.2px;line-height:25.5px}

/* contact */
.contact-bg{left:0;top:2430px;width:1200px;height:924px;background:var(--light)}
.field{position:absolute;background:var(--white);border:1px solid #dcdcdc;border-radius:22px;font-size:13px;color:#9a9a9a;padding:0 22px;display:flex;align-items:center}
.field.msg{align-items:flex-start;padding-top:20px;border-radius:20px}

/* footer */
.foot-brand{width:1200px;left:0;top:3040px;display:flex;flex-direction:column;align-items:center;gap:14px}
.foot-mark{width:70px;height:70px;border-radius:50%;border:7px solid var(--white)}
.foot-name{font-family:"Poppins",sans-serif;font-weight:600;font-size:21px;color:var(--white)}
.foot-nav{width:1200px;left:0;top:3152px;display:flex;justify-content:center;gap:28px;color:var(--white);font-size:14.5px;font-weight:500}
.foot-info{width:1200px;left:0;top:3200px;display:flex;justify-content:center;gap:26px;color:var(--white);font-size:14px}
.foot-info .item{display:flex;align-items:center;gap:8px}
.foot-rule{left:143px;top:3234px;width:912px;height:1px;background:#3a3a3a}
.copyright{width:1200px;left:0;top:3260px;text-align:center;color:var(--white);font-size:12.5px}
.socials{width:1200px;left:0;top:3297px;display:flex;justify-content:center;gap:10px}
.socials span{width:31px;height:31px;border-radius:50%;background:var(--white)}
.socials span:first-child{background:var(--mint)}
</style>
</head>
<body>

<!-- header -->
<svg class="abs topbar" width="1200" height="50" viewBox="0 0 1200 50">
  <polygon points="370,0 1200,0 1200,50 406,50" fill="var(--navy)"/>
</svg>
<div class="abs brand">
  <div class="brand-mark"></div>
  <div class="brand-name">Tollbrook<br>Advisory</div>
</div>
<div class="abs contact-chip" style="left:440px">
  <div class="chip-icon"><svg width="18" height="14" viewBox="0 0 18 14"><rect x="1" y="1" width="16" height="12" fill="none" stroke="#fff" stroke-width="1.5"/><path d="M1 1l8 7 8-7" fill="none" stroke="#fff" stroke-width="1.5"/></svg></div>
  <div><div class="chip-label">Email</div><div class="chip-value">info@tollbrookadvisory.example</div></div>
</div>
<div class="abs contact-chip" style="left:748px">
  <div class="chip-icon"><svg width="16" height="16" viewBox="0 0 16 16"><path d="M3 1l3 3-2 2c1 2 3 4 5 5l2-2 3 3-2 3C6 14 2 10 1 3z" fill="none" stroke="#fff" stroke-width="1.4"/></svg></div>
  <div><div class="chip-label">Call or text us</div><div class="chip-value">+1-555-010-4477</div></div>
</div>
<div class="abs login">
  <svg width="10" height="12" viewBox="0 0 10 12" style="margin-right:6px"><rect x="1" y="5" width="8" height="7" fill="#fff"/><path d="M3 5V3a2 2 0 014 0v2" fill="none" stroke="#fff" stroke-width="1.5"/></svg>LOGIN
</div>
<nav class="abs mainnav"><span>HOME</span><span>ABOUT US</span><span>SERVICES</span><span>TEAM</span><span style="margin:0">CONTACT US</span></nav>

<!-- hero -->
<svg class="abs" style="left:0;top:105px" width="1200" height="575" viewBox="0 0 1200 575" role="img" aria-label="Sunset view over a dense city skyline of high-rise towers">
  <defs>
    <linearGradient id="heroSky" x1="0" y1="0" x2="0" y2="1">
      <stop offset="0" stop-color="#6b5a45"/>
      <stop offset=".25" stop-color="#c79a5a"/>
      <stop offset=".55" stop-color="#5b4e42"/>
      <stop offset="1" stop-color="#2e2a27"/>
    </linearGradient>
    <linearGradient id="heroShade" x1="0" y1="0" x2="1" y2="0">
      <stop offset="0" stop-color="#1e1c1a" stop-opacity=".55"/>
      <stop offset=".5" stop-color="#1e1c1a" stop-opacity=".1"/>
      <stop offset="1" stop-color="#1e1c1a" stop-opacity="0"/>
    </linearGradient>
  </defs>
  <polygon points="0,0 1200,0 1200,403 797,552 0,426" fill="url(#heroSky)"/>
  <polygon points="0,0 1200,0 1200,403 797,552 0,426" fill="url(#heroShade)"/>
  <polygon points="0,426 797,552 1200,403 1200,418 797,570 0,436" fill="var(--mint)"/>
</svg>
<h1 class="abs heading hero-title">Building <em>Success</em> in<br>Southern California</h1>
<p class="abs hero-sub">Expertise at Every Step: From Planning to Execution</p>
<div class="btn" style="left:143px;top:359px;width:176px;height:43px;font-size:16px">Get Started <span class="dot"></span></div>

<!-- about -->
<svg class="abs" style="left:0;top:596px" width="591" height="537" viewBox="0 0 591 537" role="img" aria-label="Three colleagues in business attire reviewing plans together at a meeting table">
  <defs>
    <linearGradient id="aboutPhoto" x1="0" y1="0" x2="1" y2="1">
      <stop offset="0" stop-color="#8d9a96"/>
      <stop offset=".5" stop-color="#c9c7c2"/>
      <stop offset="1" stop-color="#e6e3df"/>
    </linearGradient>
  </defs>
  <polygon points="0,0 591,107 591,537 0,537" fill="url(#aboutPhoto)"/>
</svg>
<h2 class="abs heading about-title">About Us</h2>
<div class="abs about-text">
  <p>Welcome to Tollbrook Advisory, your trusted partner in navigating the complexities of the real estate and small business markets. Founded by industry veterans Daniel Reyes and Kevin Park, we specialize in providing comprehensive services tailored to the unique needs of our clients.</p>
  <p>Whether you're a franchisee, a new restaurant owner, or a commercial real estate investor, our expertise in due diligence, construction management, and investment property evaluation ensures you make informed, strategic decisions.</p>
</div>
<div class="btn" style="left:645px;top:1050px;width:160px;height:46px">Learn More <span class="dot"></span></div>

<!-- services -->
<h2 class="abs heading section-title" style="top:1192px">Tollbrook <span>Services</span></h2>
<div class="abs arrow" style="left:72px"><svg width="10" height="14" viewBox="0 0 10 14"><path d="M8 1L2 7l6 6" fill="none" stroke="#fff" stroke-width="2"/></svg></div>
<div class="abs arrow" style="left:1087px"><svg width="10" height="14" viewBox="0 0 10 14"><path d="M2 1l6 6-6 6" fill="none" stroke="#fff" stroke-width="2"/></svg></div>

<div class="abs service" style="left:146px">
  <div class="svc-icon"><svg width="42" height="42" viewBox="0 0 42 42" fill="none" stroke="#fff" stroke-width="2"><path d="M4 34l12-12 8 6 14-16"/><path d="M30 12h8v8"/><path d="M4 38h34"/></svg></div>
  <div class="svc-name">Franchise Development &amp; Launch</div>
  <div class="svc-desc">Comprehensive franchise setup from evaluation to launch for scalable business growth.</div>
</div>
<div class="abs service active" style="left:454px">
  <div class="svc-icon mint"><svg width="42" height="42" viewBox="0 0 42 42" fill="none" stroke="#fff" stroke-width="2"><circle cx="18" cy="18" r="11"/><path d="M26 26l11 11"/></svg></div>
  <div class="svc-name">Due Diligence</div>
  <div class="svc-desc">Conducting thorough due diligence for business and property transactions toidentify potential risks</div>
</div>
<div class="abs service" style="left:763px">
  <div class="svc-icon"><svg width="42" height="42" viewBox="0 0 42 42" fill="none" stroke="#fff" stroke-width="2"><path d="M5 20L21 6l16 14"/><path d="M10 16v20h22V16"/><rect x="18" y="25" width="6" height="11"/></svg></div>
  <div class="svc-name">Investment Property Evaluation</div>
  <div class="svc-desc">Providing detailed analysis of potential investment properties, including profitability forecasts and risk assessments.</div>
</div>

<!-- call to action -->
<div class="abs cta" role="img" aria-label="Dark tinted city skyline backdrop"></div>
<h2 class="abs heading cta-title">Unlock Your Business Potential Today!</h2>
<p class="abs cta-text">At Tollbrook Advisory, we're dedicated to turning your business aspirations into reality. Our expertise and commitment ensure you make informed, strategic decisions that drive success. Take the first step towards achieving your goals with confidence.</p>
<div class="btn" style="left:505px;top:1797px;width:191px;height:46px;font-size:14px">Get Started Now <span class="dot"></span></div>

<!-- team -->
<h2 class="abs heading section-title" style="top:1970px;color:var(--navy-2)">Our Team</h2>
<div class="abs member-name">Daniel Reyes</div>
<div class="abs member-role">Principal</div>
<div class="abs member-mail"><svg width="14" height="11" viewBox="0 0 14 11"><rect width="14" height="11" fill="#333"/><path d="M0 0l7 6 7-6" fill="none" stroke="#fff" stroke-width="1.2"/></svg>daniel@tollbrookadvisory.example</div>
<p class="abs member-bio">Daniel Reyes brings almost 20 years of rich experience as a real estate inves­tor and a pivotal role at one of southern California's largest real estate manage­ment firms, where he led sales</p>
<div class="btn" style="left:144px;top:2305px;width:160px;height:47px;font-size:14px">Learn More <span class="dot"></span></div>

<svg class="abs" style="left:377px;top:2060px" width="823" height="292" viewBox="0 0 823 292">
  <defs>
    <linearGradient id="team1" x1="0" y1="0" x2="0" y2="1"><stop offset="0" stop-color="#9fc3de"/><stop offset=".5" stop-color="#c7c9c4"/><stop offset="1" stop-color="#eef0f2"/></linearGradient>
    <linearGradient id="team2" x1="0" y1="0" x2="0" y2="1"><stop offset="0" stop-color="#8a7e6e"/><stop offset=".6" stop-color="#7a5e48"/><stop offset="1" stop-color="#2b2a2c"/></linearGradient>
    <linearGradient id="team3" x1="0" y1="0" x2="0" y2="1"><stop offset="0" stop-color="#c9c6c0"/><stop offset=".55" stop-color="#a47e62"/><stop offset="1" stop-color="#7b95b4"/></linearGradient>
  </defs>
  <polygon points="0,0 297,0 297,292 85,292" fill="url(#team1)" role="img" aria-label="Portrait of principal Daniel Reyes outdoors above a hillside town"/>
  <rect x="302" y="0" width="296" height="292" fill="url(#team2)" role="img" aria-label="Portrait of principal Kevin Park in a dark suit"/>
  <rect x="603" y="0" width="220" height="292" fill="url(#team3)" role="img" aria-label="Portrait of a team member in a blue top"/>
</svg>

<!-- contact -->
<div class="abs contact-bg"></div>
<h2 class="abs heading section-title" style="top:2484px">Contact Us</h2>
<div class="field" style="left:221px;top:2574px;width:367px;height:48px">Name</div>
<div class="field" style="left:225px;top:2638px;width:367px;height:48px">Email Address</div>
<div class="field" style="left:225px;top:2699px;width:367px;height:48px">Phone Number</div>
<div class="field msg" style="left:609px;top:2573px;width:370px;height:173px">Message</div>
<div class="btn" style="left:519px;top:2786px;width:162px;height:47px;font-size:16px;text-transform:none">Submit Now <span class="dot"></span></div>

<!-- footer -->
<svg class="abs" style="left:0;top:2885px" width="1200" height="469" viewBox="0 0 1200 469" role="img" aria-label="Dark footer backdrop with city landmark silhouettes">
  <polygon points="0,167 403,4 1200,115 1200,469 0,469" fill="var(--mint)"/>
  <polygon points="0,170 403,26 1200,134 1200,469 0,469" fill="var(--black)"/>
</svg>
<div class="abs foot-brand">
  <div class="foot-mark"></div>
  <div class="foot-name">Tollbrook Advisory</div>
</div>
<nav class="abs foot-nav"><span>HOME</span><span>/</span><span>ABOUT US</span><span>/</span><span>SERVICES</span><span>/</span><span>TEAM</span><span>/</span><span>CONTACT US</span></nav>
<div class="abs foot-info">
  <span class="item"><svg width="12" height="12" viewBox="0 0 16 16"><path d="M3 1l3 3-2 2c1 2 3 4 5 5l2-2 3 3-2 3C6 14 2 10 1 3z" fill="var(--mint)"/></svg>+1 555 010 4477</span>
  <span>|</span>
  <span class="item"><svg width="10" height="14" viewBox="0 0 10 14"><path d="M5 0a5 5 0 015 5c0 4-5 9-5 9S0 9 0 5a5 5 0 015-5z" fill="var(--mint)"/><circle cx="5" cy="5" r="2" fill="#000"/></svg>214 Harbor Point Dr Suite 300, Costa Mesa, CA 92626</span>
  <span>|</span>
  <span class="item"><svg width="14" height="11" viewBox="0 0 14 11"><rect width="14" height="11" fill="var(--mint)"/><path d="M0 0l7 6 7-6" fill="none" stroke="#000" stroke-width="1.2"/></svg>info@tollbrookadvisory.example</span>
</div>
<div class="abs foot-rule"></div>
<p class="abs copyright">Copyright© 2024 Tollbrook Advisory |&nbsp; All Rights Reserved</p>
<div class="abs socials"><span></span><span></span><span></span></div>

</body>
</html>
```